Residential Remodeling Contractor needs updated business card

I need a new design for my business card.
Name of the company is Ridgefell Construction. I need a card that commands presence, strength, integrity. I have been in business for 28 years. I am a Residential Remodeling Contractor that covers all aspects of a residential remodel and build.

```html
<!DOCTYPE html>
<html lang="en">
<head>
<meta charset="utf-8">
<title>Ridgefell Construction – Business Card</title>
<link rel="stylesheet" href="https://fonts.googleapis.com/css2?family=Open+Sans:wght@400;600;700&display=swap">
<style>
  :root {
    --backdrop: #232323;
    --card-blue: #213f7f;
    --ink-white: #ffffff;
    --rule-white: rgba(255, 255, 255, 0.85);
  }
  * { box-sizing: border-box; margin: 0; padding: 0; }
  html, body {
    width: 1200px;
    height: 780px;
    overflow: hidden;
    background: var(--backdrop);
    font-family: "Open Sans", Arial, sans-serif;
    color: var(--ink-white);
  }
  .stage {
    position: relative;
    width: 1200px;
    height: 780px;
  }
  .card {
    position: absolute;
    width: 540px;
    height: 309px;
    background: var(--card-blue);
    box-shadow: 0 10px 28px rgba(0, 0, 0, 0.6);
  }
  .card--front { left: 40px; top: 235px; }
  .card--back  { left: 620px; top: 235px; }

  .brand {
    display: flex;
    align-items: center;
    gap: 14px;
    font-weight: 600;
    letter-spacing: 0.06em;
    text-transform: uppercase;
    line-height: 1.1;
  }
  .brand__mark {
    flex: none;
    width: 18px;
    height: 18px;
    background: var(--ink-white);
  }
  .card--front .brand {
    position: absolute;
    left: 0; right: 0; top: 50%;
    transform: translateY(-50%);
    justify-content: center;
    font-size: 34px;
  }
  .card--front .brand__mark { width: 26px; height: 26px; }

  .card--back .brand {
    position: absolute;
    left: 34px;
    top: 150px;
    font-size: 20px;
  }
  .divider {
    position: absolute;
    left: 276px;
    top: 40px;
    width: 1px;
    height: 170px;
    background: var(--rule-white);
  }
  .person {
    position: absolute;
    left: 300px;
    top: 40px;
  }
  .person__name {
    font-size: 26px;
    font-weight: 700;
    line-height: 1.1;
  }
  .person__role {
    font-size: 13px;
    font-weight: 400;
    margin-top: 4px;
  }
  .contacts {
    list-style: none;
    position: absolute;
    left: 300px;
    top: 124px;
    font-size: 13px;
  }
  .contacts li {
    display: flex;
    align-items: center;
    gap: 9px;
    margin-bottom: 6px;
  }
  .contacts svg { width: 14px; height: 14px; flex: none; }
  .address {
    position: absolute;
    left: 0; right: 0;
    bottom: 24px;
    text-align: center;
    font-size: 13px;
  }
</style>
</head>
<body>
<main class="stage">
  <section class="card card--front" aria-label="Card front">
    <div class="brand">
      <span class="brand__mark"></span>
      <span class="brand__name">Ridgefell<br>Construction</span>
    </div>
  </section>

  <section class="card card--back" aria-label="Card back">
    <div class="brand">
      <span class="brand__mark"></span>
      <span class="brand__name">Ridgefell<br>Construction</span>
    </div>
    <div class="divider"></div>
    <div class="person">
      <p class="person__name">Tomas Varek</p>
      <p class="person__role">Managing Director</p>
    </div>
    <ul class="contacts">
      <li>
        <svg viewBox="0 0 16 16" aria-hidden="true"><path fill="#fff" d="M3.6 1.5l2.2 2.6-1.3 1.6c.8 1.9 2.1 3.2 4 4l1.6-1.3 2.6 2.2-1.4 2.4C6.6 12.7 3.3 9.4 1.2 4.7z"/></svg>
        <span>(555) 214-6630</span>
      </li>
      <li>
        <svg viewBox="0 0 16 16" aria-hidden="true"><rect x="1.5" y="3.5" width="13" height="9" fill="none" stroke="#fff" stroke-width="1.4"/><path d="M1.5 3.5l6.5 5 6.5-5" fill="none" stroke="#fff" stroke-width="1.4"/></svg>
        <span>info@ridgefellbuild.com</span>
      </li>
      <li>
        <svg viewBox="0 0 16 16" aria-hidden="true"><circle cx="8" cy="8" r="6.3" fill="none" stroke="#fff" stroke-width="1.4"/><ellipse cx="8" cy="8" rx="2.6" ry="6.3" fill="none" stroke="#fff" stroke-width="1.2"/><path d="M1.8 8h12.4" stroke="#fff" stroke-width="1.2"/></svg>
        <span>www.ridgefellbuild.com</span>
      </li>
    </ul>
    <p class="address">418 Cedar Hollow Rd Maplewood, Texas 75990 USA</p>
  </section>
</main>
</body>
</html>
```